Youth Lifting Youth Business Card. We have existing logo

We need a business card design from an existing logo.
Our logo is in black and white but would love to add in the color burgundy but we're open to any color. Our website is www.youthliftingyouthmv.org

Target Market(s)

corporations and foundations who will be donating

Industry/Entity Type

Business

Contact Information for Business Card

Address: 2318 Marwick Ave Carden Hills, OR 97420
Name: Corin Halvorsen
Founder email: corin.halvorsen@youthliftingyouthmv.org
Phone: 805-637-9081

Requirements
Nice to have
• Our colors are burgundy and white, but that's not a necessity

```html
<!DOCTYPE html>
<html lang="en">
<head>
<meta charset="utf-8">
<title>Youth Lifting Youth – Business Card</title>
<link rel="stylesheet" href="https://fonts.googleapis.com/css2?family=Crimson+Text:wght@400;600&display=swap">
<style>
  :root {
    --bg: #e9e6e1;
    --card: #f7f7f6;
    --card-shade: #e6e6e6;
    --ink: #2b2b2b;
    --ink-soft: #555555;
    --rule: #3a3a3a;
    --band: #141414;
    --band-grey: #6e6e6e;
    --band-light: #b8b8b8;
    --watermark: #dcdcdc;
  }
  html, body {
    margin: 0;
    width: 1200px;
    height: 818px;
    overflow: hidden;
    background: var(--bg);
  }
  .canvas {
    position: relative;
    width: 1200px;
    height: 818px;
  }
  .card {
    position: absolute;
    left: 180px;
    top: 169px;
    width: 840px;
    height: 480px;
    background: radial-gradient(ellipse at 40% 45%, #ffffff 0%, var(--card) 55%, var(--card-shade) 100%);
    box-shadow: 0 10px 30px rgba(0,0,0,0.18);
    overflow: hidden;
    font-family: "Crimson Text", Georgia, serif;
    color: var(--ink);
  }
  .tree-mark {
    position: absolute;
    left: 450px;
    top: 30px;
    width: 250px;
    height: 230px;
    border-radius: 48% 52% 40% 44%;
    background: radial-gradient(ellipse at 50% 40%, var(--watermark) 0%, #e8e8e8 60%, rgba(240,240,240,0) 100%);
  }
  .logo {
    position: absolute;
    left: 44px;
    top: 48px;
    display: flex;
    align-items: center;
    gap: 16px;
  }
  .logo-disc {
    width: 96px;
    height: 96px;
    border-radius: 50%;
    border: 3px solid var(--ink);
    box-sizing: border-box;
  }
  .logo-name {
    font-size: 24px;
    font-weight: 400;
    color: var(--ink);
  }
  .top-rule {
    position: absolute;
    left: 600px;
    top: 234px;
    width: 200px;
    height: 2px;
    background: var(--rule);
  }
  .identity {
    position: absolute;
    left: 44px;
    top: 246px;
    width: 520px;
  }
  .identity .name-row {
    display: flex;
    align-items: center;
    gap: 16px;
  }
  .identity .name {
    font-size: 38px;
    font-weight: 600;
    letter-spacing: 0.5px;
    white-space: nowrap;
  }
  .identity .name-rule {
    flex: 1;
    height: 2px;
    background: var(--rule);
  }
  .identity .role {
    font-size: 25px;
    color: var(--ink-soft);
    margin-top: -4px;
  }
  .address {
    position: absolute;
    right: 40px;
    top: 260px;
    text-align: right;
    font-size: 23px;
    line-height: 1.3;
  }
  .contacts {
    position: absolute;
    left: 44px;
    top: 346px;
    font-size: 21px;
    line-height: 1.45;
  }
  .contacts .line {
    display: flex;
    align-items: center;
    gap: 12px;
  }
  .contacts svg { flex: none; }
  .band {
    position: absolute;
    left: 0;
    bottom: 0;
  }
</style>
</head>
<body>
<div class="canvas">
  <div class="card">
    <div class="tree-mark" role="img" aria-label="Faint tree silhouette watermark"></div>

    <div class="logo">
      <div class="logo-disc"></div>
      <div class="logo-name">Youth Lifting Youth</div>
    </div>

    <div class="top-rule"></div>

    <div class="identity">
      <div class="name-row">
        <div class="name">Corin Halvorsen</div>
        <div class="name-rule"></div>
      </div>
      <div class="role">Founder</div>
    </div>

    <div class="address">
      2318 Marwick Ave<br>
      Carden Hills, OR 97420
    </div>

    <div class="contacts">
      <div class="line">
        <svg width="22" height="22" viewBox="0 0 22 22" aria-hidden="true">
          <rect width="22" height="22" rx="2" fill="#8a8a8a"/>
          <path d="M7 5c1 0 1.6 2.4 1.4 3.2-.2.7-1.3 1-1 1.8.6 1.6 1.9 2.9 3.4 3.6.8.3 1.2-.8 1.9-1 .8-.2 3.2.6 3.2 1.5 0 1.2-1.3 2.4-2.6 2.4C9 16.5 5.5 13 5.3 7.8 5.2 6.3 6 5 7 5z" fill="#fff"/>
        </svg>
        <span>805-637-9081</span>
      </div>
      <div class="line">
        <svg width="22" height="22" viewBox="0 0 22 22" aria-hidden="true">
          <rect width="22" height="22" rx="2" fill="#8a8a8a"/>
          <rect x="4" y="6" width="14" height="10" fill="none" stroke="#fff" stroke-width="1.4"/>
          <path d="M4 6l7 6 7-6M4 16l5-5M18 16l-5-5" fill="none" stroke="#fff" stroke-width="1.2"/>
        </svg>
        <span>corin.halvorsen@youthliftingyouthmv.org</span>
      </div>
    </div>

    <svg class="band" width="840" height="56" viewBox="0 0 840 56" aria-hidden="true">
      <polygon points="0,6 540,6 556,18 0,18" fill="var(--band-light)"/>
      <polygon points="0,18 556,18 572,30 0,30" fill="var(--band-grey)"/>
      <rect x="0" y="32" width="840" height="24" fill="var(--band)"/>
    </svg>
  </div>
</div>
</body>
</html>
```